Business card design for a teacher - double sided, sleek design.

My name is Lina and I am an online Arabic language teacher. I am looking for a beautiful business card design for my online teaching business.

The cards will be printed in 85mm x 55mm size.
The card can be either portrait or landscape.

The design should contain my logo on one side and information on the other.

The design needs to be clean and modern. Use of subtle Arabic geometric patterns would be nice. Icons for the social media information on the card should also match the design theme.

My logo font is Consolas, which is a Monospace font.

Business card design should be delivered with editable PSD or EPS files in the handover.

Thanks

Lina

----

Information on the back:

URL: www.speakwithnadia.net [this should stand out more than other details]
Email: info@speakwithnadia.net
Instagram: @speakwithnadia
Facebook: facebook.com/speakwithnadia
Skype: speakwithnadia

My brand colours are shown in the logo attached. These are:
- Teal green - 4DC9C1
- Mango yellow - FFD600

Target Market(s)

- Young professionals
- Expatriates
- Women and Men

Industry/Entity Type

Education

Contact Information for Business Card

Information on the back:

Skype: speakwithnadia

- Teal green - 4DC9C1
- Mango yellow - FFD600

Font styles to use
Other font styles liked:
• Any font complimentary to my logo font which is a Monospace font called Consolas.

Colors

Designer to choose colors to be used in the design.

Requirements
Must have
• - Aesthetically pleasing look
• - Complimentary design with existing logo
Nice to have
• Arabic geometrical patterns

```html
<!DOCTYPE html>
<html lang="en">
<head>
<meta charset="utf-8">
<title>Lina — Business Card</title>
<link href="https://fonts.googleapis.com/css2?family=Inconsolata:wght@600&family=Open+Sans:wght@400&display=swap" rel="stylesheet">
<style>
  :root {
    --teal: #4dc9c1;
    --teal-deep: #45bdb5;
    --teal-light: #5fd0c9;
    --paper: #f6f7f7;
    --ink: #ffffff;
    --stage: #e9e7e3;
  }
  * { margin: 0; padding: 0; box-sizing: border-box; }
  html, body { width: 1200px; height: 886px; overflow: hidden; }
  body {
    background: var(--stage);
    position: relative;
    font-family: "Open Sans", sans-serif;
  }
  .card {
    position: absolute;
    top: 275px;
    width: 520px;
    height: 336px;
    box-shadow: 0 6px 18px rgba(0,0,0,0.18);
    overflow: hidden;
  }
  .card--front { left: 60px; display: flex; }
  .card--back { left: 620px; background: var(--teal); }

  /* Front: identity area */
  .identity {
    width: 42%;
    background: var(--paper);
    display: flex;
    align-items: center;
    justify-content: center;
    gap: 12px;
  }
  .identity__dot {
    width: 16px;
    height: 16px;
    border-radius: 50%;
    background: var(--teal);
    flex: none;
  }
  .identity__name {
    font-family: "Inconsolata", monospace;
    font-weight: 600;
    font-size: 34px;
    line-height: 1;
    color: var(--teal);
    letter-spacing: 4px;
  }

  /* Front: contact area */
  .contacts {
    width: 58%;
    background: var(--teal);
    display: flex;
    flex-direction: column;
    justify-content: center;
    padding-left: 32px;
    gap: 6px;
    list-style: none;
  }
  .contacts li {
    display: flex;
    align-items: center;
    gap: 9px;
    color: var(--ink);
    font-size: 13px;
    white-space: nowrap;
  }
  .contacts__mark {
    width: 9px;
    height: 9px;
    border-radius: 2px;
    background: var(--ink);
    flex: none;
  }
  .contacts .contacts__url { font-size: 14px; }

  /* Back */
  .back__pattern {
    position: absolute;
    inset: 0;
    background: linear-gradient(135deg, var(--teal-light), var(--teal-deep));
  }
  .back__mark {
    position: absolute;
    left: 50%;
    top: 50%;
    transform: translate(-50%, -50%);
    display: flex;
    flex-direction: column;
    align-items: center;
    gap: 18px;
  }
  .back__name {
    font-family: "Inconsolata", monospace;
    font-weight: 600;
    font-size: 52px;
    line-height: 1;
    color: var(--ink);
    letter-spacing: 6px;
  }
  .back__url {
    font-family: "Inconsolata", monospace;
    font-weight: 600;
    font-size: 14px;
    color: var(--ink);
    letter-spacing: 2px;
  }
</style>
</head>
<body>
  <section class="card card--front">
    <div class="identity">
      <span class="identity__dot"></span>
      <div class="identity__name">LINA</div>
    </div>
    <ul class="contacts">
      <li><span class="contacts__mark"></span>info@speakwithnadia.net</li>
      <li><span class="contacts__mark"></span>@speakwithnadia</li>
      <li><span class="contacts__mark"></span>facebook.com/speakwithnadia</li>
      <li><span class="contacts__mark"></span>speakwithnadia</li>
      <li class="contacts__url"><span class="contacts__mark"></span>www.speakwithnadia.net</li>
    </ul>
  </section>

  <section class="card card--back">
    <div class="back__pattern" role="img" aria-label="Subtle repeating Arabic geometric pattern in teal tones"></div>
    <div class="back__mark">
      <div class="back__name">LINA</div>
      <div class="back__url">www.speakwithnadia.net</div>
    </div>
  </section>
</body>
</html>
```